Online Shop Maren

We need a web design for an online shop, called "Lirvo Dune Jewels". The shop should have an extraordinary, elegant look, as shown in the Quellwick Advertising Picture in our Briefing.pdf (attached). Please have a look at our Briefing regarding website colours, background ideas, and elements to be included. The online shop is about professional jewellery design pieces, where each piece is handmade of high quality materials, also unique pieces and unique editions possible. It should attract extraordinary people and visualize that its a very individual and unique design jewellery. You can get an idea of whom it should attract by reading our target group. Colours to be used are jewellery-Velvet red, Black / anthracite, exclusive colours, silverish-white, bronze-brown and golden.

Please play around when designing with the image pictures we attach, preferably more vertical pictures, no panoramic pictures like in Brovenka Shop. Also include the BLACK logo of lirvo dune. We include the SITEMAP in the briefing and also another folder with product pictures you can use for the draft.

Regarding Functions, the store will have the SAME (technical) functions as this page:http://www.brovenka-shop.eu/ - using the "most famous" products/categories for the starting page, going into individual product pages by clicking these images and then leading to a detailed page for one product only.

Target Market(s)

Jewellery-lovers, who appreciate extraordinary things, creative economy/fashion-industries, stylists, Style consultants, outfitter, theatres, operas, production sites, Cocktail-, Dinner and Bridefashion, exclusive traditional costume stores, dancesports and tango argento dancers

Industry/Entity Type

Shop

Requirements
Must have
• Must include:
• Colours as per briefing
• Background ideas/images as per briefing/pictures sent
• Sitemap as per briefing
• Social buttons
• Logo
• Design for 3 pages: Starting page showing big images, attractive design and the 4 popular categories
• Subpage with different products of one category (i.e. bracelets)
• Detail page with one individual product only
Should not have
• no fresh, playful colours like yellow, orange, green, blue
• no cheap design, no panorama pictures

```html
<!DOCTYPE html>
<html lang="en">
<head>
<meta charset="utf-8">
<title>Lirvo Dune Jewels – Online Shop</title>
<link rel="stylesheet" href="https://fonts.googleapis.com/css2?family=Open+Sans:wght@400;600;700&family=Oswald:wght@400;600&family=Roboto:wght@400;500&family=Cinzel:wght@700&display=swap">
<style>
:root{
  --red:#e0141e;
  --red-deep:#c8101a;
  --ink:#2b2b2b;
  --muted:#777;
  --light:#f3f3f3;
  --line:#dcdcdc;
  --panel:#2e2e31;
  --page-dark:#1c1c1c;
  --foot-dark:#111;
  --foot-text:#8a8a8a;
  --white:#fff;
  --link-blue:#3a3a7a;
  --pink:#e8165f;
}
*{box-sizing:border-box;margin:0;padding:0}
html,body{width:1200px;height:2594px;overflow:hidden}
body{position:relative;background:var(--page-dark);font-family:"Open Sans",Arial,sans-serif;color:var(--ink)}
.abs{position:absolute}
ul{list-style:none}

/* top bar */
.topbar{left:0;top:0;width:1200px;height:45px;background:var(--light);font-family:Georgia,serif;font-size:13px;color:#888}
.topbar .acct{left:110px;top:14px}
.topbar .acct span,.topbar .nav span{padding:0 14px;border-left:1px solid #bbb}
.topbar .acct span:first-child{padding-left:0;border-left:0}
.topbar .nav{right:110px;top:14px}
.topbar .nav span:first-child{border-left:0}
.topbar .nav .hot{color:var(--red)}

/* header */
.header{left:0;top:45px;width:1200px;height:121px;background:var(--white)}
.brand{left:110px;top:26px;display:flex;align-items:center;gap:12px}
.brand-mark{width:10px;height:10px;background:var(--red)}
.brand-name{font-family:"Open Sans",sans-serif;font-weight:400;color:#1a1a1a;font-size:28px;line-height:30px;text-align:center}
.brand-name small{display:block;font-size:14px;line-height:18px}
.search{left:750px;top:31px;width:232px;height:29px;border:1px solid #ccc;border-radius:15px;font-size:11px;color:#999;padding:7px 14px}
.search svg{position:absolute;right:10px;top:6px}
.basket{left:1008px;top:26px;font-size:14px;color:#444;display:flex;gap:8px;align-items:center}
.tel{left:895px;top:76px;font-size:16px;color:#555;display:flex;gap:8px;align-items:center;font-family:Roboto,Arial,sans-serif}

/* hero */
.hero{left:0;top:166px;width:1200px;height:479px;background:linear-gradient(90deg,#7a7a5e 0%,#8c8468 30%,#6e5d55 55%,#54415a 75%,#3a3150 100%)}
.hero-copy{left:110px;top:105px;width:370px}
.hero-title{font-family:Oswald,sans-serif;font-weight:400;color:var(--red);font-size:46px;line-height:52px;letter-spacing:1px}
.hero-sub{font-family:Oswald,sans-serif;font-weight:600;color:#fff;font-size:26px;line-height:34px;margin-top:6px}
.hero-text{font-size:12px;line-height:16px;color:#e6e2d8;margin-top:8px}
.hero-more{font-family:Oswald,sans-serif;font-weight:600;color:var(--red);font-size:19px;margin-top:20px;display:flex;align-items:center;gap:10px}

/* main panel */
.main{left:95px;top:645px;width:1008px;height:1539px;background:var(--white)}
.promo{top:17px;width:311px;height:138px;color:#fff;font-family:Georgia,serif}
.promo h3{position:absolute;font-weight:400;font-size:20px;letter-spacing:1px}
.promo p{position:absolute;font-size:13px;line-height:23px}
.promo-1{left:15px;background:linear-gradient(90deg,#3c2a44 0%,#4e3049 45%,#b52430 100%)}
.promo-2{left:349px;background:linear-gradient(90deg,#c9c9c9 0%,#6a4a56 40%,#4d3040 100%)}
.promo-3{left:683px;background:linear-gradient(90deg,#d6cdc4 0%,#4f3e4f 40%,#3c2f44 100%)}

.cats{left:15px;top:195px;width:276px;height:197px;background:var(--panel);color:#fff;padding:14px 16px}
.cats h4{font-weight:400;font-size:20px;letter-spacing:.5px}
.cats li{font-size:17px;line-height:30px;padding-left:16px;position:relative}
.cats li:before{content:"";position:absolute;left:2px;top:14px;width:3px;height:3px;background:#aaa}
.cats ul{margin-top:10px}

.latest{left:15px;top:427px;width:276px;height:389px;border:1px solid var(--line);padding:0 18px}
.latest h4{position:absolute;left:17px;top:22px;font-weight:400;font-size:19px;letter-spacing:.5px}
.latest .arrows{position:absolute;right:18px;top:23px;display:flex;gap:4px}
.latest .rule{position:absolute;left:26px;right:26px;top:55px;border-top:1px solid var(--line)}
.latest .ph{position:absolute;left:26px;top:63px;width:227px;height:216px;background:radial-gradient(circle at 50% 45%,#6a6a6a,#2a2a2a 75%)}
.latest .name{position:absolute;left:0;right:0;top:296px;text-align:center;font-size:13px;color:var(--link-blue)}
.btn-dark{position:absolute;left:105px;top:329px;width:101px;height:35px;background:#333;color:#fff;font-size:12px;text-align:center;line-height:35px;font-family:Arial,sans-serif}

.offer{left:15px;top:851px;width:276px;height:327px;background:linear-gradient(160deg,#cfc7c2 0%,#8a7672 45%,#3e3236 100%)}
.offer-band{left:0;bottom:0;width:276px;height:59px;background:rgba(20,20,20,.85);color:#fff;font-family:Cinzel,serif;font-weight:700;font-size:20px;line-height:26px;text-align:center;padding-top:4px;letter-spacing:1px}

.featured-head{left:311px;top:205px;width:682px}
.featured-head h2{font-size:23px;font-weight:600;color:#222;background:#fff;display:inline-block;padding-right:14px;position:relative;z-index:1}
.featured-head .rule{position:absolute;left:0;top:16px;width:560px;border-top:1px solid var(--line)}
.view-all{left:866px;top:207px;width:127px;height:32px;border:1px solid #ccc;border-radius:3px;font-size:11px;color:#c0392b;text-align:center;line-height:30px;box-shadow:0 1px 2px rgba(0,0,0,.15)}

.card{width:205px;height:368px;border:1px solid var(--line);background:#fff}
.card .ph{position:absolute;left:0;top:0;width:203px;height:287px}
.card .label{position:absolute;left:4px;top:262px;color:#fff;font-size:15px;font-family:Arial,sans-serif;letter-spacing:.5px}
.card .price{position:absolute;right:0;top:251px;height:34px;padding:0 8px 0 22px;background:var(--red);color:#fff;font-size:20px;line-height:34px;font-family:Arial,sans-serif;clip-path:polygon(14px 0,100% 0,100% 100%,14px 100%,0 50%)}
.card .actions{position:absolute;left:28px;top:308px;display:flex;gap:12px;align-items:center}
.card .actions ul{font-size:10px;color:#777;line-height:20px}
.ico-circle{width:38px;height:38px;border-radius:50%;background:#555;display:flex;align-items:center;justify-content:center}

.ph-pearl{background:radial-gradient(ellipse at 50% 45%,#6d6d6d 0%,#3a3a3a 45%,#161616 85%)}
.ph-gold{background:radial-gradient(ellipse at 50% 45%,#9a8c6a 0%,#555 40%,#1c1c1c 85%)}
.ph-silver{background:radial-gradient(ellipse at 50% 45%,#8a8a8a 0%,#444 45%,#181818 85%)}
.ph-black{background:radial-gradient(ellipse at 50% 50%,#4a3f30 0%,#2a2a2a 45%,#111 85%)}

.info{top:1089px;width:312px;height:91px;border:2px solid #e55;display:flex;align-items:center;padding-left:22px;gap:16px}
.info .ring{width:48px;height:48px;border:1px solid #ccc;border-radius:50%;display:flex;align-items:center;justify-content:center}
.info h5{font-size:18px;font-weight:400;color:#333;font-family:Roboto,Arial,sans-serif}
.info h5 b{color:var(--red);font-weight:700}
.info p{font-size:10px;color:#666;margin-top:3px;font-family:Roboto,Arial,sans-serif}

.f-title{font-family:Roboto,Arial,sans-serif;font-size:17px;color:#ccc;font-weight:400;letter-spacing:.5px}
.small{font-size:10px;line-height:14px;color:#777;font-family:Arial,sans-serif}
.about{left:40px;top:1244px;width:195px}
.about .small{margin-top:6px}
.contact-row{display:flex;align-items:center;gap:10px;margin-top:14px}
.dot-red{width:26px;height:26px;border-radius:50%;background:var(--red);display:flex;align-items:center;justify-content:center;flex:none}
.news{left:282px;top:1244px;width:330px}
.news-item{display:flex;gap:12px;margin-top:16px}
.news-item .thumb{width:50px;height:46px;flex:none;background:linear-gradient(180deg,#ddd,#555)}
.news-item .meta{font-style:italic;color:#555}
.socials{left:747px;top:1253px;width:230px}
.soc-grid{display:grid;grid-template-columns:98px 98px;column-gap:20px;row-gap:10px}
.soc{height:33px;background:#2f3033;border-radius:3px;color:#fff;font-size:11px;display:flex;align-items:center;gap:8px;padding-left:4px;font-family:Arial,sans-serif}
.soc i{width:22px;height:22px;display:block;background:#5b6f8a}
.soc.r i{background:#c0392b}
.newsletter{margin-top:30px}
.newsletter .f-title{color:#bbb}
.news-form{display:flex;margin-top:10px}
.news-form .field{width:154px;height:23px;background:#111;color:#888;font-size:9px;font-style:italic;line-height:23px;padding-left:8px}
.news-form .go{width:60px;height:23px;background:var(--pink);color:#fff;font-size:10px;text-align:center;line-height:23px}

/* dark footer */
.footer{left:0;top:2184px;width:1200px;height:323px;background:linear-gradient(180deg,#121212,#0d0d0d)}
.f-col{top:56px}
.f-col .f-title{font-size:17px;color:#9fb3c8}
.f-col .small{color:#aaa}
.f-list{margin-top:18px;width:200px}
.f-list li{font-size:11px;color:#8fa3b5;line-height:30px;border-bottom:1px solid #222;padding-left:14px;position:relative;font-family:Arial,sans-serif}
.f-list li:before{content:"";position:absolute;left:2px;top:14px;width:3px;height:3px;background:#666}
.pay{display:flex;gap:14px;margin-top:28px;font-family:Arial,sans-serif;font-weight:700;font-size:14px;color:#5f86b8}
.bottombar{left:0;top:2507px;width:1200px;height:87px;background:#0b0b0b;border-top:1px solid #1e1e1e}
.b-social{left:110px;top:17px;display:flex;gap:18px}
.b-social span{width:27px;height:27px;border-radius:50%;background:#334a66}
.copy{right:133px;top:33px;font-size:10px;color:#666;font-family:Arial,sans-serif}
</style>
</head>
<body>

<div class="topbar abs">
  <div class="acct abs"><span>Login</span><span>Create An Account</span></div>
  <div class="nav abs"><span>Home</span><span>Wish List (0)</span><span>My Account</span><span class="hot">Shopping Cart</span><span>Checkout</span></div>
</div>

<header class="header abs">
  <div class="brand abs">
    <div class="brand-mark"></div>
    <div class="brand-name">Lirvo Dune<small>Jewels</small></div>
  </div>
  <div class="search abs">Search
    <svg width="16" height="16" viewBox="0 0 16 16"><circle cx="6.5" cy="6.5" r="5" fill="none" stroke="#aaa" stroke-width="1.5"/><line x1="10" y1="10" x2="14.5" y2="14.5" stroke="#aaa" stroke-width="1.5"/></svg>
  </div>
  <div class="basket abs">
    <svg width="26" height="22" viewBox="0 0 26 22"><path d="M1 2h4l3 12h13l3-9H7" fill="none" stroke="#e0141e" stroke-width="2"/><circle cx="10" cy="18" r="2" fill="#e0141e"/><circle cx="19" cy="18" r="2" fill="#e0141e"/></svg>
    Basket
  </div>
  <div class="tel abs">
    <svg width="18" height="18" viewBox="0 0 18 18"><path d="M4 1l3 4-2 2c1 2.5 3 4.5 5.5 5.5l2-2 4 3-2 3C8 16 2 10 1 4z" fill="#555"/></svg>
    Tel: (+00) 4821.905.316
  </div>
</header>

<section class="hero abs" role="img" aria-label="Banner photo of a woman in a red dress wearing earrings and a bracelet">
  <div class="hero-copy abs">
    <h1 class="hero-title">KIWI RINGS<br>REVOLUTION</h1>
    <div class="hero-sub">LOREM IPSUM DOLOR - SIT AMET</div>
    <p class="hero-text">Lorem Ipsum is simply dummy text of the printing and typesetting industry. Lorem Ipsum has been the industry's standard dummy text ever since the 1500s. Lorem Ipsum is simply dummy text of the printing and typesetting industry.</p>
    <div class="hero-more">READ MORE <svg width="10" height="12" viewBox="0 0 10 12"><path d="M1 0l8 6-8 6z" fill="#e0141e"/></svg></div>
  </div>
</section>

<main class="main abs">
  <div class="promo promo-1 abs" role="img" aria-label="Promo banner with model in red dress">
    <h3 style="left:14px;top:10px">NEW FASHION</h3>
    <p style="left:16px;top:42px">Only From<br>$14.00</p>
  </div>
  <div class="promo promo-2 abs" role="img" aria-label="Promo banner with model in white hat">
    <h3 style="right:12px;top:10px">CELEBRATE</h3>
    <p style="left:176px;top:42px">Special Offer For<br>Womens Only<br>$170.00</p>
  </div>
  <div class="promo promo-3 abs" role="img" aria-label="Promo banner with model wearing a necklace">
    <h3 style="left:132px;top:10px;font-size:17px">NEW COLLECTION</h3>
    <p style="left:132px;top:40px">Just only for womens<br>its special offer<br>$130.00</p>
  </div>

  <nav class="cats abs">
    <h4>PRODUCTS</h4>
    <ul><li>Collier</li><li>Bracelet</li><li>Ring</li><li>Earring</li></ul>
  </nav>

  <aside class="latest abs">
    <h4>LATEST PRODUCTS</h4>
    <div class="arrows">
      <svg width="22" height="22" viewBox="0 0 22 22"><circle cx="11" cy="11" r="11" fill="#999"/><path d="M13 6l-5 5 5 5" fill="none" stroke="#fff" stroke-width="2"/></svg>
      <svg width="22" height="22" viewBox="0 0 22 22"><circle cx="11" cy="11" r="11" fill="#999"/><path d="M9 6l5 5-5 5" fill="none" stroke="#fff" stroke-width="2"/></svg>
    </div>
    <div class="rule"></div>
    <div class="ph" role="img" aria-label="Crystal bead collier on black background"></div>
    <div class="name">Halvern Men's Automatic1</div>
    <div class="btn-dark">Add to Cart</div>
  </aside>

  <div class="offer abs" role="img" aria-label="Photo of a woman wearing a pearl necklace and bracelet">
    <div class="offer-band abs">Special Offer<br>For Women</div>
  </div>

  <div class="featured-head abs"><div class="rule"></div><h2>Featured Products</h2></div>
  <div class="view-all abs">View All Products</div>

  <!-- product grid -->
  <article class="card abs" style="left:315px;top:258px">
    <div class="ph ph-pearl" role="img" aria-label="Pearl drop earrings"></div>
    <span class="label">OHRRINGE</span><span class="price">33€</span>
    <div class="actions"><div class="ico-circle"><svg width="18" height="16" viewBox="0 0 18 16"><path d="M1 6h16l-2 9H3z M5 6l4-5 4 5" fill="#fff"/></svg></div><ul><li>+ Add to Wishlist</li><li>+Add to Compare</li></ul></div>
  </article>
  <article class="card abs" style="left:553px;top:258px">
    <div class="ph ph-silver" role="img" aria-label="Crystal and gold bead bracelet"></div>
    <span class="label">COLLIER</span><span class="price">55 €</span>
    <div class="actions"><div class="ico-circle"><svg width="18" height="16" viewBox="0 0 18 16"><path d="M1 6h16l-2 9H3z M5 6l4-5 4 5" fill="#fff"/></svg></div><ul><li>+ Add to Wishlist</li><li>+Add to Compare</li></ul></div>
  </article>
  <article class="card abs" style="left:790px;top:258px">
    <div class="ph ph-silver" role="img" aria-label="Beaded pendant with tassel"></div>
    <span class="label">ANHÄNGER</span><span class="price">275€</span>
    <div class="actions"><div class="ico-circle"><svg width="18" height="16" viewBox="0 0 18 16"><path d="M1 6h16l-2 9H3z M5 6l4-5 4 5" fill="#fff"/></svg></div><ul><li>+ Add to Wishlist</li><li>+Add to Compare</li></ul></div>
  </article>
  <article class="card abs" style="left:315px;top:678px">
    <div class="ph ph-gold" role="img" aria-label="Gold beaded necklace"></div>
    <span class="label">OHRRINGE</span><span class="price">110€</span>
    <div class="actions"><div class="ico-circle"><svg width="18" height="16" viewBox="0 0 18 16"><path d="M1 6h16l-2 9H3z M5 6l4-5 4 5" fill="#fff"/></svg></div><ul><li>+ Add to Wishlist</li><li>+Add to Compare</li></ul></div>
  </article>
  <article class="card abs" style="left:553px;top:678px">
    <div class="ph ph-black" role="img" aria-label="Black and gold bead armband"></div>
    <span class="label">ARMBAND</span><span class="price">330€</span>
    <div class="actions"><div class="ico-circle"><svg width="18" height="16" viewBox="0 0 18 16"><path d="M1 6h16l-2 9H3z M5 6l4-5 4 5" fill="#fff"/></svg></div><ul><li>+ Add to Wishlist</li><li>+Add to Compare</li></ul></div>
  </article>
  <article class="card abs" style="left:790px;top:678px">
    <div class="ph ph-silver" role="img" aria-label="Crystal collier"></div>
    <span class="label" style="font-size:13px;top:265px">COLLIER KRISTALL</span><span class="price">330€</span>
    <div class="actions"><div class="ico-circle"><svg width="18" height="16" viewBox="0 0 18 16"><path d="M1 6h16l-2 9H3z M5 6l4-5 4 5" fill="#fff"/></svg></div><ul><li>+ Add to Wishlist</li><li>+Add to Compare</li></ul></div>
  </article>

  <div class="info abs" style="left:311px">
    <div class="ring"><svg width="24" height="20" viewBox="0 0 24 20"><path d="M2 6c0-3 20-3 20 0v2h-5V6H7v2H2z M5 9h14l2 10H3z" fill="#555"/><circle cx="12" cy="14" r="2.5" fill="#fff"/></svg></div>
    <div><h5><b>ONLINE</b> &nbsp;ORDERS</h5><p>ORDERS BY PHONE&nbsp; (+94) 70318-552</p></div>
  </div>
  <div class="info abs" style="left:683px">
    <div class="ring"><svg width="26" height="18" viewBox="0 0 26 18"><path d="M1 2h15v11H1z M16 6h5l4 4v3h-9z" fill="#555"/><circle cx="6" cy="15" r="2.5" fill="#555"/><circle cx="20" cy="15" r="2.5" fill="#555"/></svg></div>
    <div><h5><b>FREE</b> &nbsp;SHIPPING</h5><p>ON YOUR ORDERS OVER $500.00</p></div>
  </div>

  <section class="about abs">
    <h6 class="f-title" style="color:#ccc">ABOUT US</h6>
    <p class="small">Lorem ipsum dolor sit amet, consectetur adipiscing elit. Quisque lacinia laoreet Quisque gravida tempor velit. Quisque lacinia laoreet Quisque gravida.</p>
    <div class="contact-row"><span class="dot-red"><svg width="12" height="12" viewBox="0 0 18 18"><path d="M4 1l3 4-2 2c1 2.5 3 4.5 5.5 5.5l2-2 4 3-2 3C8 16 2 10 1 4z" fill="#fff"/></svg></span><span style="font-size:14px;color:#777">(+80) 274 615 930</span></div>
    <div class="contact-row"><span class="dot-red"><svg width="12" height="12" viewBox="0 0 12 12"><path d="M6 1L1 6h2v5h6V6h2z" fill="#fff"/></svg></span><span class="small">5087 - Corven Lane. Bandit Aliquam</span></div>
    <div class="contact-row"><span class="dot-red"><svg width="12" height="10" viewBox="0 0 12 10"><path d="M0 0h12v10H0z" fill="#fff"/><path d="M0 0l6 5 6-5" fill="none" stroke="#e0141e"/></svg></span><span class="small">support@lirvomail.com</span></div>
  </section>

  <section class="news abs">
    <h6 class="f-title" style="color:#ccc">LATEST NEWS</h6>
    <div class="news-item"><div class="thumb" role="img" aria-label="Small news photo"></div><p class="small">Lorem ipsum dolor sit amet, consectetur adipiscing elit. Quisque lacinia laoreet Quisque gravida tempor velit.<br><span class="meta">15 minutes ago l Post by Doranvel</span></p></div>
    <div class="news-item"><div class="thumb" role="img" aria-label="Small news photo"></div><p class="small">Lorem ipsum dolor sit amet, consectetur adipiscing elit. Quisque lacinia laoreet Quisque gravida tempor velit.<br><span class="meta">15 minutes ago l Post by Doranvel</span></p></div>
    <div class="news-item"><div class="thumb" role="img" aria-label="Small news photo"></div><p class="small">Lorem ipsum dolor sit amet, consectetur adipiscing elit. Quisque lacinia laoreet Quisque gravida tempor velit.<br><span class="meta">15 minutes ago l Post by Doranvel</span></p></div>
  </section>

  <section class="socials abs">
    <div class="soc-grid">
      <div class="soc"><i></i>Netlink</div>
      <div class="soc"><i></i>Friendbook</div>
      <div class="soc r"><i></i>Globeplus</div>
      <div class="soc"><i></i>Chirper</div>
    </div>
    <div class="newsletter">
      <h6 class="f-title">NEWSLETTER</h6>
      <p class="small" style="margin-top:8px">Lorem ipsum dolor sit amet, consectetur adipiscing elit. Donec tristique, nisi vitae.</p>
      <div class="news-form"><div class="field">Your Email</div><div class="go">SIGN UP</div></div>
    </div>
  </section>
</main>

<footer class="footer abs">
  <div class="f-col abs" style="left:110px;width:200px">
    <h6 class="f-title">LATEST TWEETS</h6>
    <p class="small" style="margin-top:24px">Lorem ipsum dolor sit amet, consectetur adipiscing elit.</p>
    <p class="small" style="margin-top:14px">Praesent a enim neque. Fusce eleifend massa ut diam pretium at tincidunt metus tempus.</p>
    <p class="small" style="margin-top:26px">Lorem ipsum dolor sit amet, consectetur adipiscing elit.</p>
  </div>
  <div class="f-col abs" style="left:359px">
    <h6 class="f-title">INFORMATION</h6>
    <ul class="f-list"><li>About us</li><li>Delivery Information</li><li>Privacy Policy</li><li>Terms &amp; Condition</li><li>Contact Us</li></ul>
  </div>
  <div class="f-col abs" style="left:607px">
    <h6 class="f-title">CUSTOMER SERVICE</h6>
    <ul class="f-list"><li>My Account</li><li>Order History</li><li>Wish List</li><li>Newsletter</li><li>Returns</li><li>Site Map</li></ul>
  </div>
  <div class="f-col abs" style="left:856px;width:240px">
    <h6 class="f-title">CONTACT US</h6>
    <p class="small" style="margin-top:24px;color:#8fa3b5">5087 - Corven Lane. Bandit Tringi Aliquam Vitae. New York</p>
    <div style="display:flex;gap:14px;align-items:center;margin-top:20px;font-size:15px;color:#ccc;font-family:Roboto,Arial,sans-serif">
      <svg width="22" height="22" viewBox="0 0 22 22"><rect width="22" height="22" rx="3" fill="#e8165f"/><path d="M7 4l2 3-1.5 1.5c.8 2 2.2 3.4 4 4.2L13 11l3 2-1.5 3C10 15.5 6 11.5 5.5 6z" fill="#fff"/></svg>
      (+80) 274 615 930
    </div>
    <div class="pay"><span>Vexa</span><span>Mastro</span><span>Cirrel</span><span>PayNova</span></div>
  </div>
</footer>

<div class="bottombar abs">
  <div class="b-social abs"><span></span><span></span><span></span><span></span></div>
  <div class="copy abs">© 2013 Powered by Lirvo Dune-Jewels. All Rights Reserved.</div>
</div>

</body>
</html>
```